Business Card Design needed for start up company Halvora

In need of a new business card designed for a start up company based in Sydney, Halvora is a new start up innovative Company, our mission it to make property accessible for everyday Australian and to become the leading Real Estate platform in Australia. We want it to be fresh and clean.

Industry/Entity Type

Financial

Contact Information for Business Card

Section for Name
Section for Title

HALVORA - The Strength of Pooling
Mobile:
Direct:

Font styles to use
Sans Serif

Colors
33a6d7
0692cd
0255a3
ffffff

Requirements
Must have
• Logo, all business card details

```html
<!DOCTYPE html>
<html lang="en">
<head>
<meta charset="utf-8">
<title>Halvora Business Card</title>
<link rel="stylesheet" href="https://fonts.googleapis.com/css2?family=Poppins:wght@300;400;500;600;700&display=swap">
<style>
  :root {
    --sky: #33a6d7;
    --azure: #0692cd;
    --navy: #0255a3;
    --white: #ffffff;
    --ink: #333a44;
    --muted: #8a8f96;
    --ghost: #e8e8e8;
    --stage: #2b2d31;
  }
  * { box-sizing: border-box; margin: 0; padding: 0; }
  html, body {
    width: 1200px; height: 1000px; overflow: hidden;
    background: var(--stage);
    font-family: "Poppins", Arial, sans-serif;
  }
  .canvas { position: relative; width: 1200px; height: 1000px; }
  .card {
    position: absolute; left: 250px; width: 700px; height: 400px;
    border-radius: 30px; overflow: hidden;
  }
  /* Front */
  .card-front {
    top: 60px;
    background: linear-gradient(35deg, var(--navy) 0%, var(--azure) 55%, var(--sky) 100%);
  }
  .front-brand {
    position: absolute; left: 0; right: 0; top: 150px;
    display: flex; justify-content: center; align-items: center; gap: 18px;
  }
  .front-brand .brand-dot {
    width: 90px; height: 90px; border-radius: 50%; background: var(--white);
  }
  .front-brand .brand-name {
    color: var(--white); font-weight: 700; font-size: 68px; letter-spacing: 1px; line-height: 1;
  }
  .tagline {
    position: absolute; left: 0; right: 0; bottom: 42px; text-align: center;
    color: var(--white); font-size: 13px; font-weight: 400; letter-spacing: 6px;
  }
  /* Back */
  .card-back { top: 540px; background: var(--white); }
  .ghost-circle {
    position: absolute; right: 50px; top: 40px;
    width: 200px; height: 200px; border-radius: 50%; background: var(--ghost);
  }
  .back-brand {
    position: absolute; left: 36px; top: 42px;
    display: flex; align-items: flex-start; gap: 14px;
  }
  .back-brand .brand-dot {
    width: 118px; height: 118px; border-radius: 50%; background: var(--sky); margin-top: 26px;
  }
  .back-brand .brand-name {
    color: var(--navy); font-weight: 700; font-size: 60px; line-height: 1; letter-spacing: 1px;
  }
  .person { position: absolute; left: 176px; top: 118px; }
  .person-name { font-size: 30px; font-weight: 600; line-height: 1.1; }
  .person-name .first { color: var(--navy); }
  .person-name .last { color: var(--sky); font-weight: 500; }
  .person-title { color: var(--muted); font-size: 14px; margin-top: 4px; }
  .title-rule { width: 44px; height: 3px; background: var(--navy); margin-top: 10px; }
  .contacts {
    position: absolute; left: 176px; top: 218px; list-style: none;
    color: var(--ink); font-size: 16px; line-height: 26px;
  }
  .contacts li { display: flex; align-items: center; gap: 12px; }
  .contacts svg { width: 14px; height: 14px; fill: var(--azure); flex: none; }
  .contacts .accent { color: var(--sky); }
  .address { position: absolute; left: 202px; top: 330px; font-size: 15px; line-height: 20px; }
  .address-label { color: var(--sky); font-weight: 500; }
  .address-line { color: var(--ink); }
</style>
</head>
<body>
<main class="canvas">
  <section class="card card-front">
    <div class="front-brand">
      <span class="brand-dot"></span>
      <span class="brand-name">HALVORA</span>
    </div>
    <p class="tagline">THE STRENGTH OF POOLING</p>
  </section>

  <section class="card card-back">
    <span class="ghost-circle"></span>
    <div class="back-brand">
      <span class="brand-dot"></span>
      <span class="brand-name">HALVORA</span>
    </div>
    <div class="person">
      <h1 class="person-name"><span class="first">Marlen</span> <span class="last">Hayes</span></h1>
      <p class="person-title">Director</p>
      <div class="title-rule"></div>
    </div>
    <ul class="contacts">
      <li>
        <svg viewBox="0 0 24 24" aria-hidden="true"><path d="M6.6 10.8a15 15 0 0 0 6.6 6.6l2.2-2.2c.3-.3.7-.4 1-.2 1.1.4 2.3.6 3.6.6.6 0 1 .4 1 1V20c0 .6-.4 1-1 1A17 17 0 0 1 3 4c0-.6.4-1 1-1h3.5c.6 0 1 .4 1 1 0 1.3.2 2.5.6 3.6.1.3 0 .7-.2 1z"/></svg>
        000 123 456 789
      </li>
      <li>
        <svg viewBox="0 0 24 24" aria-hidden="true"><path d="M7 1h10a2 2 0 0 1 2 2v18a2 2 0 0 1-2 2H7a2 2 0 0 1-2-2V3a2 2 0 0 1 2-2zm0 3v14h10V4zm5 15.5a1 1 0 1 0 0 2 1 1 0 0 0 0-2z"/></svg>
        000 222 3334
      </li>
      <li>
        <svg viewBox="0 0 24 24" aria-hidden="true"><path d="M2 5h20v14H2zm2 2v.5l8 5 8-5V7zm0 2.8V17h16V9.8l-8 5z"/></svg>
        urname@email.com
      </li>
      <li>
        <svg viewBox="0 0 24 24" aria-hidden="true"><path d="M12 2a10 10 0 1 0 0 20 10 10 0 0 0 0-20zm6.9 6h-2.9a15 15 0 0 0-1.4-3.6A8 8 0 0 1 18.9 8zM12 4c.8 1.2 1.5 2.5 1.9 4h-3.8c.4-1.5 1.1-2.8 1.9-4zM4.3 14a8 8 0 0 1 0-4h3.4a16 16 0 0 0 0 4zm.8 2h2.9c.3 1.3.8 2.5 1.4 3.6A8 8 0 0 1 5.1 16zM8 8H5.1a8 8 0 0 1 4.3-3.6C8.8 5.5 8.3 6.7 8 8zm4 12c-.8-1.2-1.5-2.5-1.9-4h3.8c-.4 1.5-1.1 2.8-1.9 4zm2.3-6H9.7a14 14 0 0 1 0-4h4.6a14 14 0 0 1 0 4zm.3 5.6c.6-1.1 1.1-2.3 1.4-3.6h2.9a8 8 0 0 1-4.3 3.6zm1.7-5.6a16 16 0 0 0 0-4h3.4a8 8 0 0 1 0 4z"/></svg>
        <span>www.<span class="accent">websitename</span>.com</span>
      </li>
    </ul>
    <div class="address">
      <p class="address-label">Address:</p>
      <p class="address-line">Your Street Address, Singapore, 1234</p>
    </div>
  </section>
</main>
</body>
</html>
```